Business Cards for IT Consulting Company (Managed Service Provider)

I am looking to have some business cards printed and would like some designs. We are an IT Consulting company based in Vancouver BC. I would like a nice clean and modern look to the cards. I have uploaded all the versions of my logo so parts can be used as needed. Here is a snippit from our website homepage:

Quillbrook Networks Ltd. is an IT Solutions Partner located in Vancouver BC, Canada. We offer IT solutions and support to customers in the greater Vancouver Area. With expertise in Microsoft platforms, as well as Linux and Mac OSX and over 12 years experience in the IT industry, Quillbrook Networks is dedicated to offering our clients top quality service and products. We take pride in the solutions we offer our customers. The greatest compliment a client can give us is to recommend our services.

Quillbrook Networks Ltd. offers a wide range of IT services from onsite service to remote support and managed service solutions. This allows clients to choose the support path that best suits their company’s needs. Supporting many different sized companies from small to enterprise level over the past 12 years Quillbrook Networks has the experience and expertise needed to ensure things run smoothly. Allowing our clients to focus on doing business.

Revolutionizing the way IT services are delivered.

Quillbrook Networks is dedicated to providing our clients with IT solutions that work and grow with them for years to come. This philosophy helps save money in the long run instead of replacing equipment constantly. Far too often IT solutions are not well thought out and while possibly solving the problem at hand, require replacement due to growth or quality within a very short time frame. Quillbrook Networks takes pride in providing solutions that will last and be able to accommodate growth without the need for replacement.

Industry/Entity Type

Information Technology

Contact Information for Business Card

Quillbrook Networks Ltd.
(Employee Name)
Eml: (Employees Email Address)
Web: quillbrook.me
Ph: 604-555-0148

Font styles to use
Serif
Sans Serif

Requirements
Must have
• The Company logo and company colors.
Nice to have
• - Our tag line: "Revolutionizing IT Services" or "Revolutionizing the way IT services are delivered."
• - Also I really like the idea of nature and technology together blending which is sort of where my logo came from so integrating that somehow onto the business cards would be great.

```html
<!DOCTYPE html>
<html lang="en">
<head>
<meta charset="UTF-8">
<title>Quillbrook Networks Ltd. – Business Card</title>
<link rel="stylesheet" href="https://fonts.googleapis.com/css2?family=Montserrat:wght@400;500;600;700&display=swap">
<style>
  :root {
    --brand-blue: #1aa7e8;
    --ink: #4a4a4a;
    --ink-dark: #333333;
    --card: #ffffff;
    --backdrop: #2b2b2d;
  }
  * { margin: 0; padding: 0; box-sizing: border-box; }
  html, body {
    width: 1200px;
    height: 900px;
    overflow: hidden;
    background: var(--backdrop);
    font-family: "Montserrat", Arial, sans-serif;
  }
  .card {
    position: absolute;
    width: 700px;
    height: 400px;
    background: var(--card);
    border-radius: 26px;
    overflow: hidden;
    box-shadow: 0 14px 30px rgba(0,0,0,0.45);
  }

  /* Front side */
  .card-front { left: 90px; top: 40px; }
  .front-brand {
    position: absolute;
    left: 0; right: 0; top: 130px;
    display: flex;
    align-items: center;
    justify-content: center;
    gap: 16px;
  }
  .brand-square {
    width: 34px; height: 34px;
    background: var(--brand-blue);
  }
  .front-name {
    color: var(--brand-blue);
    font-weight: 600;
    font-size: 38px;
    letter-spacing: 0.5px;
  }
  .tagline {
    position: absolute;
    left: 0; right: 0; top: 290px;
    text-align: center;
    color: var(--ink);
    font-size: 17px;
    font-weight: 500;
    letter-spacing: 1.6px;
  }

  /* Back side */
  .card-back { left: 410px; top: 470px; }
  .edge-band {
    position: absolute;
    right: 0; top: 0;
    width: 24px; height: 185px;
    background: var(--brand-blue);
    border-bottom-left-radius: 24px;
  }
  .back-brand {
    position: absolute;
    left: 50px; top: 200px;
    display: flex;
    align-items: center;
    gap: 14px;
  }
  .back-brand .brand-square { width: 28px; height: 28px; }
  .back-name {
    color: var(--brand-blue);
    font-weight: 600;
    font-size: 24px;
    line-height: 1.15;
    width: 250px;
  }
  .divider {
    position: absolute;
    left: 370px; top: 120px;
    width: 2px; height: 150px;
    background: var(--brand-blue);
  }
  .person {
    position: absolute;
    left: 392px; top: 118px;
  }
  .person-name {
    color: var(--brand-blue);
    font-weight: 700;
    font-size: 25px;
    letter-spacing: 1.5px;
  }
  .person-title {
    color: var(--ink-dark);
    font-weight: 600;
    font-size: 14px;
    letter-spacing: 1.5px;
    margin-top: 2px;
  }
  .contact-list {
    list-style: none;
    margin-top: 18px;
  }
  .contact-list li {
    display: flex;
    align-items: center;
    gap: 10px;
    color: var(--ink-dark);
    font-size: 15px;
    font-weight: 500;
    letter-spacing: 0.8px;
    margin-bottom: 7px;
  }
  .contact-list svg { width: 12px; height: 12px; flex: none; }
</style>
</head>
<body>

<section class="card card-front" aria-label="Card front">
  <div class="front-brand">
    <span class="brand-square"></span>
    <span class="front-name">Quillbrook Networks</span>
  </div>
  <p class="tagline">Revolutionizing IT Services</p>
</section>

<section class="card card-back" aria-label="Card back">
  <div class="edge-band"></div>

  <div class="back-brand">
    <span class="brand-square"></span>
    <span class="back-name">Quillbrook Networks Ltd.</span>
  </div>

  <div class="divider"></div>

  <div class="person">
    <h1 class="person-name">MARIN KELLER</h1>
    <p class="person-title">DIRECTOR</p>
    <ul class="contact-list">
      <li>
        <svg viewBox="0 0 24 24" fill="#1aa7e8" aria-hidden="true"><path d="M6.6 10.8a15 15 0 0 0 6.6 6.6l2.2-2.2c.3-.3.7-.4 1-.2 1.1.4 2.3.6 3.6.6.6 0 1 .4 1 1V20c0 .6-.4 1-1 1C10.6 21 3 13.4 3 4c0-.6.4-1 1-1h3.5c.6 0 1 .4 1 1 0 1.3.2 2.5.6 3.6.1.3 0 .7-.2 1z"/></svg>
        604-555-0148
      </li>
      <li>
        <svg viewBox="0 0 24 24" fill="none" stroke="#1aa7e8" stroke-width="2.5" aria-hidden="true"><rect x="2" y="5" width="20" height="14" rx="2"/><path d="M2 6l10 7 10-7"/></svg>
        info@marinkeller.com
      </li>
      <li>
        <svg viewBox="0 0 24 24" fill="#1aa7e8" aria-hidden="true"><circle cx="12" cy="12" r="10"/><path d="M2 12h20M12 2c3 3 3 17 0 20M12 2c-3 3-3 17 0 20" stroke="#fff" stroke-width="1.5" fill="none"/></svg>
        www.quillbrook.me
      </li>
    </ul>
  </div>
</section>

</body>
</html>
```